All Natural Mosquito Repellent

My company, BrightPebble Company has created an all natural mosquito repellent. I already have other all natural products that I have developed and created labels for. I will include a copy of that label so you have something to work from. I will need two labels. One for the front of the bottle and one for the back. The back label will need space for a UPC. The labels need to be 63mm (H) x 39mm (W)

Target Market(s)

Consumers, Organic, People who like natural products

Font styles to use
Other font styles liked:
• A combination of both Serif and Sans Serif

Requirements
Must have
• Use the words Organic, All Natural, Travel size, made in the USA label
Nice to have
• tag line: Don't beat them off. Spray them away.

```html
<!DOCTYPE html>
<html lang="en">
<head>
<meta charset="utf-8">
<title>BrightPebble Company – Mosquito Repellent Labels</title>
<link href="https://fonts.googleapis.com/css2?family=Oswald:wght@400;500;600&family=Open+Sans:wght@400;600;700&display=swap" rel="stylesheet">
<style>
  :root{
    --bg:#e4e4e6;
    --forest:#083a1c;
    --forest-deep:#052a12;
    --orange-hi:#fbc21c;
    --orange:#f6921e;
    --orange-deep:#ee7a1a;
    --rust:#b94a26;
    --cream:#ffffff;
    --ink-soft:#e8efe9;
    --name:#5a4638;
  }
  *{box-sizing:border-box;margin:0;padding:0}
  html,body{width:1200px;height:1200px;overflow:hidden}
  body{background:radial-gradient(circle at 50% 40%,#f7f7f8 0%,var(--bg) 70%);font-family:"Open Sans",sans-serif;position:relative}
  .label{position:absolute;top:309px;width:360px;height:582px;border-radius:10px;overflow:hidden;background:var(--forest);color:var(--cream);box-shadow:0 10px 30px rgba(0,0,0,.18)}
  .label--front{left:200px}
  .label--back{left:640px}

  /* front */
  .sky{position:absolute;left:0;top:0;width:100%;height:232px;background:radial-gradient(ellipse at 50% 60%,var(--orange-hi) 0%,var(--orange) 55%,var(--orange-deep) 100%)}
  .brand-mark{position:absolute;left:50%;top:38px;width:86px;height:86px;margin-left:-43px;border-radius:50%;background:var(--name);opacity:.85}
  .brand-name{position:absolute;top:124px;width:100%;text-align:center;font-family:"Open Sans",sans-serif;font-weight:400;font-size:19px;letter-spacing:.5px;color:var(--name)}
  .brand-sub{position:absolute;top:148px;width:100%;text-align:center;font-size:7px;color:var(--name)}
  .treeline{position:absolute;left:0;top:150px;width:100%;height:88px;background:linear-gradient(to bottom,rgba(8,58,28,0) 0%,rgba(8,58,28,.75) 45%,var(--forest) 100%)}
  .banner{position:absolute;left:42px;top:213px;width:270px;height:48px;background:var(--rust);display:flex;align-items:center;justify-content:center;font-family:"Oswald",sans-serif;font-weight:600;font-size:28px;letter-spacing:-.3px;color:var(--cream)}
  .claims{position:absolute;top:264px;width:100%;text-align:center;font-family:"Oswald",sans-serif;font-weight:500;font-size:12px;color:var(--cream);letter-spacing:.2px}
  .claims span.dot{display:inline-block;width:6px;height:6px;border-radius:50%;background:var(--cream);margin:0 9px;vertical-align:2px}
  .swoosh{position:absolute;left:0;top:0}
  .tagline{position:absolute;top:340px;width:100%;text-align:center;font-family:"Oswald",sans-serif;font-weight:400;font-style:italic;font-size:21px;line-height:28px;color:var(--cream)}
  .ground{position:absolute;left:0;top:0}
  .shield{position:absolute;left:148px;top:442px}
  .volume{position:absolute;left:296px;top:459px;font-family:"Oswald",sans-serif;font-weight:500;font-size:12px}
  .stamp{position:absolute;left:36px;top:488px;transform:rotate(-16deg);font-family:"Oswald",sans-serif;font-weight:600;font-size:13px;line-height:12px;color:var(--rust);text-align:center;-webkit-text-stroke:.4px var(--cream);paint-order:stroke}
  .origin{position:absolute;top:548px;width:100%;text-align:center;font-size:15px;color:var(--cream)}

  /* back */
  .section{position:absolute;left:0;width:100%;text-align:center}
  .section__title{display:inline-block;border:1px solid var(--cream);border-radius:3px;padding:2px 7px;font-weight:700;font-size:10px;letter-spacing:.1px}
  .section__body{margin:8px auto 0;width:310px;font-size:7.3px;line-height:11.8px;color:var(--ink-soft)}
  .address{position:absolute;top:402px;left:0;width:100%}
  .address__title{text-align:center;font-weight:600;font-size:13px}
  .address__body{margin:8px 0 0 85px;font-size:10.5px;line-height:15px}
  .recycle{position:absolute;left:20px;top:508px}
  .upc{position:absolute;left:93px;top:496px;width:240px;height:72px;border:2px solid var(--cream);display:flex;align-items:center;justify-content:center;font-weight:600;font-size:24px}
</style>
</head>
<body>

<section class="label label--front" aria-label="Front label">
  <div class="sky"></div>
  <div class="brand-mark"></div>
  <div class="brand-name">BRIGHTPEBBLE CO.</div>
  <div class="brand-sub">crafted by hand, with love &nbsp;&nbsp;&nbsp;&nbsp;&nbsp;&nbsp; in the U.S.A.</div>
  <div class="treeline" role="img" aria-label="Silhouette of a pine forest skyline"></div>
  <div class="banner">MOSQUITO REPELLENT</div>
  <div class="claims">ALL NATURAL<span class="dot"></span>ORGANIC<span class="dot"></span>TRAVEL SIZE</div>

  <svg class="swoosh" width="360" height="582" aria-hidden="true">
    <path d="M138 330 Q180 306 228 316 Q182 312 138 330Z" fill="#fff"/>
    <path d="M135 395 Q160 412 226 394 Q170 406 135 395Z" fill="#fff"/>
  </svg>
  <p class="tagline">“Don't beat them off<br>Spray them away”</p>

  <svg class="ground" width="360" height="582" aria-hidden="true">
    <path d="M0 556 Q170 488 360 532 L360 582 L0 582Z" fill="var(--forest-deep)"/>
    <path d="M8 550 Q170 486 352 528" fill="none" stroke="#cfd6d1" stroke-width="1.4"/>
  </svg>
  <svg class="shield" width="78" height="82" viewBox="0 0 78 82" role="img" aria-label="Shield badge with mosquito">
    <path d="M4 6 Q39 -2 74 6 L72 42 Q66 66 39 80 Q12 66 6 42Z" fill="#f3f4f3" stroke="#c9ccca" stroke-width="3"/>
  </svg>
  <div class="volume">50 ML</div>
  <div class="stamp">12 HOUR<br>PROTECTION</div>
  <div class="origin">Made in the USA</div>
</section>

<section class="label label--back" aria-label="Back label">
  <div class="section" style="top:40px">
    <span class="section__title">DIRECTION FOR USE:</span>
    <p class="section__body">There are many variations of passages of Lorem Ipsum available, but the majority have suffered alteration in some form, by injected humour, or randomised words which don't look even slightly believable. If you are going to use a passage of Lorem Ipsum, you need to be sure there isn't anything embarrassing hidden in the middle of text.</p>
  </div>
  <div class="section" style="top:145px">
    <span class="section__title">PRECAUTION:</span>
    <p class="section__body">There are many variations of passages of Lorem Ipsum available, but the majority have suffered alteration in some form, by injected humour, or randomised words which don't look even slightly believable.</p>
  </div>
  <div class="section" style="top:229px">
    <span class="section__title">INGREDIENTS:</span>
    <p class="section__body">There are many variations of passages of Lorem Ipsum available, but the majority have suffered alteration in some form, by injected humour, or randomised words which don't look even slightly believable.</p>
  </div>
  <div class="section" style="top:313px">
    <span class="section__title">STORAGE:</span>
    <p class="section__body" style="width:230px">Store in a cool and dry place. Place empty container in trsh or recycle.</p>
  </div>
  <div class="address">
    <p class="address__title">Company Address:</p>
    <p class="address__body">Lorem Ipsum is simply dummy<br>text of the printing and typesetting<br>industry.</p>
  </div>
  <svg class="recycle" width="48" height="46" viewBox="0 0 48 46" role="img" aria-label="Recycle symbol">
    <g fill="none" stroke="#fff" stroke-width="5" stroke-linejoin="round">
      <path d="M14 20 L22 7 L30 20"/>
      <path d="M36 28 L28 41 L14 41"/>
      <path d="M10 30 L6 38 L18 38"/>
    </g>
    <g fill="#fff">
      <path d="M26 12 L36 14 L32 24Z"/>
      <path d="M18 35 L12 44 L10 34Z"/>
      <path d="M40 34 L34 26 L44 26Z"/>
    </g>
  </svg>
  <div class="upc">UPC</div>
</section>

</body>
</html>
```